Banner to be displayed at local Farmers Market Booth.

Graphic Design Brief: Farmers Market Banner Contest

Project Overview:We are seeking talented graphic designers to create a visually appealing banner for our booth at the local farmers market. Our company specializes in healthy, all-natural dog and cat treats, and we want a banner that captures our brand identity while drawing in pet owners who value quality and nutrition for their furry friends.

Banner Specifications:

Size: 24 inches x 60 inches (Horizontal orientation) 24" High X 60 wide

Theme: Vintage/Retro

Style: Warm, inviting, nostalgic with a touch of rustic charm

Colors: Earthy, muted tones such as warm browns, soft greens, and creamy yellows. Pops of red or blue may be used sparingly for accents. OR Black and White with gray scales. Would like to see both

Typography: Retro-style fonts that are readable and align with the vintage aesthetic.

Key Elements to Include: website (www.moltbyfarms.com)

Company Name: Moltby Farms

Tagline: " Simply Honest Bites "
Imagery: Illustrations or stylized graphics of happy dogs and cats, possibly interacting with treats.

Emphasis on Natural Ingredients: Icons or design elements that subtly suggest freshness and quality (e.g., leaves, wheat, bones, or paw prints).

Farmers Market Appeal: A design that blends well with the artisanal, handmade, and farm-fresh atmosphere of the market.

Design Considerations:

The banner should be easily readable from a distance.

A balanced composition that doesn't feel overcrowded.

Should evoke trust and warmth while maintaining a professional look.

Avoid overly modern or sleek elements that don’t align with the vintage aesthetic.

Submission Requirements:

High-resolution digital file in PDF or AI format.

CMYK color mode for printing purposes.

Must include a mockup or preview of how it would look in a real farmers market setting.

We look forward to seeing your creative interpretations of our brand! If you have any questions, feel free to reach out.

Font styles to use
Other font styles liked:
• See attachement

Requirements
Nice to have
• Retro/Vintage,playful BUT NOT whimsical

```html
<!DOCTYPE html>
<html lang="en">
<head>
<meta charset="utf-8">
<title>Moltby Farms – Market Banner</title>
<link rel="stylesheet" href="https://fonts.googleapis.com/css2?family=Rubik+Mono+One&family=Libre+Caslon+Text:wght@400;700&display=swap">
<style>
  :root {
    --page: #ffffff;
    --ink: #0b0b0b;
    --chalk: #f4f4f2;
    --lime: #dbe82c;
    --fur-light: #d9d9d6;
    --fur-dark: #5a5a58;
  }
  html, body {
    margin: 0;
    width: 1200px;
    height: 576px;
    overflow: hidden;
    background: var(--page);
  }
  .canvas {
    position: relative;
    width: 1200px;
    height: 576px;
  }
  .banner {
    position: absolute;
    left: 78px;
    top: 61px;
    width: 1064px;
    height: 425px;
    overflow: hidden;
  }
  .banner-art {
    position: absolute;
    inset: 0;
    width: 100%;
    height: 100%;
  }
  .tagline {
    position: absolute;
    left: 37px;
    top: 90px;
    width: 588px;
    margin: 0;
    font-family: "Rubik Mono One", sans-serif;
    font-weight: 400;
    color: var(--chalk);
    line-height: 1;
  }
  .tagline-line {
    display: block;
    font-size: 46px;
    letter-spacing: -1px;
    white-space: nowrap;
  }
  .tagline-line--second {
    text-align: right;
    margin-top: 16px;
  }
  .website {
    position: absolute;
    left: 81px;
    top: 222px;
    width: 517px;
    margin: 0;
    font-family: "Libre Caslon Text", serif;
    font-weight: 400;
    font-size: 26px;
    letter-spacing: 5.2px;
    color: var(--chalk);
    text-align: center;
    white-space: nowrap;
  }
  .company-name {
    position: absolute;
    left: 32px;
    top: 312px;
    margin: 0;
    font-family: "Libre Caslon Text", serif;
    font-weight: 700;
    font-size: 48px;
    letter-spacing: 6px;
    color: var(--ink);
    text-shadow: -3px 3px 0 var(--chalk);
    white-space: nowrap;
  }
  .company-line {
    position: absolute;
    left: 32px;
    top: 373px;
    margin: 0;
    font-family: "Libre Caslon Text", serif;
    font-weight: 700;
    font-size: 37.5px;
    letter-spacing: 0.2px;
    color: var(--ink);
    white-space: nowrap;
  }
  .pets-illustration {
    position: absolute;
    left: 647px;
    top: 42px;
    width: 410px;
    height: 277px;
    border-radius: 46% 40% 8px 8px / 40% 46% 8px 8px;
    background: radial-gradient(ellipse at 40% 45%, var(--fur-light) 0%, #a8a8a5 55%, var(--fur-dark) 100%);
  }
  .brand-mark {
    position: absolute;
    left: 918px;
    top: 44px;
    display: flex;
    align-items: center;
    gap: 6px;
    font-family: "Libre Caslon Text", serif;
    font-weight: 400;
    font-size: 17px;
    color: var(--chalk);
    white-space: nowrap;
  }
  .brand-dot {
    width: 9px;
    height: 9px;
    border-radius: 50%;
    background: var(--chalk);
  }
</style>
</head>
<body>
<main class="canvas">
  <section class="banner">
    <svg class="banner-art" viewBox="0 0 1064 425" preserveAspectRatio="none" aria-hidden="true">
      <defs>
        <filter id="grain" x="0" y="0" width="100%" height="100%">
          <feTurbulence type="fractalNoise" baseFrequency="0.9" numOctaves="2" seed="7" result="noise"/>
          <feColorMatrix in="noise" type="matrix"
            values="0 0 0 0 1  0 0 0 0 1  0 0 0 0 1  0 0 0 -2.2 1.15" result="specks"/>
          <feComposite in="specks" in2="SourceGraphic" operator="in"/>
        </filter>
      </defs>
      <rect class="ink-field" x="0" y="0" width="1064" height="425" fill="var(--ink)"/>
      <rect x="0" y="0" width="1064" height="425" fill="#fff" opacity="0.35" filter="url(#grain)"/>
      <path class="lime-band" fill="var(--lime)"
        d="M0 300 L18 296 L30 292 L46 297 L62 290 L80 286 L96 290 L104 284 L120 286 L134 298
           L150 303 L170 297 L188 304 L206 300 L224 306 L240 296 L256 290 L272 294 L290 284
           L306 280 L326 286 L344 284 L360 292 L378 296 L396 290 L414 296 L430 292 L444 280
           L462 274 L480 282 L496 276 L514 278 L530 286 L548 290 L566 282 L584 286 L602 280
           L620 288 L640 284 L660 292 L680 290 L700 296 L720 300 L760 306 L820 312 L880 316
           L940 314 L990 318 L1030 316 L1064 320 L1064 425 L0 425 Z"/>
    </svg>

    <h1 class="tagline">
      <span class="tagline-line">SIMPLY HONEST</span>
      <span class="tagline-line tagline-line--second">BITES</span>
    </h1>

    <p class="website">WWW.MOLTBYFARMS.COM</p>

    <div class="pets-illustration" role="img" aria-label="Black and white drawing of a dog and a tabby cat lying side by side"></div>

    <div class="brand-mark">
      <span class="brand-dot"></span>
      <span class="brand-name">Moltby Farms</span>
    </div>

    <h2 class="company-name">MOLTBY FARMS</h2>
    <p class="company-line">PURVEYORS OF PREMIUM PET FOOD &amp; TREATS</p>
  </section>
</main>
</body>
</html>
```